Modern, clean and professional Wordpress design for a safety training company!

We are currently in the process of creating a new website for our business. We have hired a website developer and the main structure of our new Wordpress site is complete. We now need an overall design plan for the site. We need a very clean, professional and easy to follow website. Most of our website visitors only spend about 30-45 secs on our sites "shopping " so it is imperative that we have a strong Home Page.
Our company specializes in CPR and First Aid Certification Classes to businesses and individuals throughout Northern California. We provide these certifications two ways: ONSITE-We come to you, and HOSTED-we offer weekly classes at our 2 locations.
Our design needs to use the general green and blue colors of our logo. But we also like white.
The final design MUST communicate a legitimate, trustworthy and professional business. Our industry is VERY competitive and we need to STAND OUT.
Currently, the NEW website that we need a new design for is www.LifelineDrillWorks.com
Our old website is www.RescuePrepValleyHub.com and we really do like the design of this website, but we just needed a Wordpress site for SEO purposes.
These are 3 websites that we really:
http://morvaliontech.com/
http://www.tralbex.com/
https://www.plivant.com/
I have attached our Logo and other images if you need to use them but looking at the current two sites will be you best help.
Target Market(s)
1) Large businesses and industries that are looking for a company to provide ONSITE safety training classes at their office or place of work.
2) Individuals that need certifications for their jobs and other needs. These individuals are looking for a legitimate, trustworthy and professional environment to complete their training class.

```html
<!DOCTYPE html>
<html lang="en">
<head>
<meta charset="utf-8">
<title>Valley Rescue Academy – CPR &amp; First Aid Certification</title>
<link href="https://fonts.googleapis.com/css2?family=Open+Sans:wght@300;400;600;700&display=swap" rel="stylesheet">
<style>
:root{
  --blue:#0b2a8c;
  --blue-dark:#061d6b;
  --blue-deep:#04155a;
  --green:#86b51b;
  --green-dark:#6f9a10;
  --text:#3a3f4a;
  --muted:#7a808c;
  --line:#4a78c6;
  --grey-bg:#f4f4f4;
  --white:#ffffff;
  --star:#f2c200;
}
*{margin:0;padding:0;box-sizing:border-box}
html,body{width:1200px;height:2276px;overflow:hidden}
body{font-family:'Open Sans',sans-serif;color:var(--text);background:var(--white);position:relative}
.abs{position:absolute}

/* header */
.topline{left:0;top:0;width:1200px;height:3px;background:var(--blue)}
.brand{left:60px;top:40px;display:flex;align-items:center;gap:12px}
.brand-dot{width:44px;height:44px;border-radius:50%;background:var(--green)}
.brand-name{font-size:27px;font-weight:700;color:var(--blue);line-height:1.05;width:200px}
.contact-bar{top:44px;left:760px;display:flex;gap:40px;font-size:13px;color:var(--text);align-items:center}
.contact-bar span{display:flex;align-items:center;gap:12px}
.contact-bar .sep{width:1px;height:22px;background:#ddd}
.badge{left:1110px;top:28px;width:32px;height:50px;background:var(--blue);border-radius:3px}
.nav{top:90px;left:354px;display:flex;height:62px;font-size:13.5px;color:#222}
.nav a{display:flex;align-items:center;padding:0 24px;text-decoration:none;color:#222;border-top:3px solid transparent}
.nav a.active{background:#f2f2f2;border-top-color:var(--green);padding:0 30px}

/* hero */
.hero{left:0;top:152px;width:1200px;height:570px;background:linear-gradient(160deg,#d9dde0 0%,#b8b2a6 35%,#6d5b4d 70%,#3e352f 100%)}
.hero-arrow{top:421px;width:34px;height:34px;border-radius:50%;background:rgba(255,255,255,.35);display:flex;align-items:center;justify-content:center}
.hero-tag{left:60px;top:590px;width:653px;height:50px;background:var(--green);color:#fff;font-size:19px;font-weight:600;display:flex;align-items:center;padding-left:18px}

/* feature boxes */
.features{left:60px;top:672px;display:flex;gap:2px}
.feature{width:268px;height:200px;background:var(--blue);color:#fff;padding:14px 22px;position:relative}
.feature:last-child{background:var(--blue-dark)}
.feature::after{content:"";position:absolute;right:0;bottom:0;border-style:solid;border-width:0 0 26px 26px;border-color:transparent transparent #3d6ac8 transparent}
.feature h3{font-weight:400;font-size:22px;margin-bottom:10px}
.feature p,.feature li{font-size:11.5px;line-height:1.6}
.feature ul{list-style:none}
.feature li::before{content:"";display:inline-block;width:7px;height:7px;background:#fff;border-radius:50%;margin-right:12px;vertical-align:middle}
.btn-white{display:inline-block;margin-top:12px;background:#fff;color:#222;font-size:11.5px;padding:6px 12px}
.btn-outline{display:inline-block;margin-top:12px;border:1px solid #fff;color:#fff;font-size:11.5px;padding:5px 11px}
.sched-row{display:flex;justify-content:space-between;font-size:11.5px;padding:13px 0;border-bottom:1px solid rgba(255,255,255,.15)}
.sched-row:last-child{border:0}

/* about */
.about-title{top:930px;left:0;width:1200px;text-align:center;font-size:33px;font-weight:300;color:#333}
.about-text{top:988px;left:215px;width:770px;text-align:center;font-size:12px;line-height:1.65;color:var(--muted)}
.plans{top:1060px;left:60px;display:flex;gap:32px}
.plan{width:242px}
.plan h2{font-weight:400;font-size:33px;color:#222;padding:0 0 2px 14px;border-bottom:1px solid var(--line);width:242px}
.plan .price{font-size:20px;padding:10px 0 0 16px;color:#222}
.plan .icons{display:flex;gap:50px;padding:20px 0 0 22px}
.plan .labels{font-size:13px;color:var(--muted);padding:4px 0 0 14px}
.plan .labels i{font-style:normal;margin:0 12px}
.plan .time{font-size:13px;color:var(--muted);padding:10px 0 12px 14px;border-bottom:1px solid var(--line)}
.plan .links{font-size:12.5px;padding:14px 0 0 14px;color:#333}
.plan .links span{margin-right:26px}
.plan .links .go{color:var(--green-dark);text-decoration:underline}

/* news & reviews */
.lower{top:1345px;left:0;width:1200px;height:610px;background:var(--grey-bg)}
.sec-title{font-size:33px;font-weight:300;color:#222}
.news-item{position:absolute;left:60px;width:512px}
.news-thumb{position:absolute;left:0;top:0;width:82px;height:82px;background:linear-gradient(135deg,#b9c6d2,#3c5578)}
.news-body{position:absolute;left:100px;top:0;width:412px}
.news-body h4{font-weight:400;font-size:23px;color:#222}
.meta{display:flex;gap:26px;font-size:11px;color:#333;margin:6px 0 12px}
.meta span{display:flex;align-items:center;gap:6px}
.news-body p{font-size:12px;line-height:1.6;color:var(--muted)}
.posted{font-size:10px;color:var(--muted);margin-top:30px;padding-bottom:14px;border-bottom:1px solid #d6d6d6}
.show-all{font-size:12px;color:var(--blue)}
.review{position:absolute;left:625px;width:512px;height:150px;border-bottom:1px solid #d6d6d6}
.avatar{position:absolute;left:0;top:0;width:82px;height:82px;border-radius:50%;background:linear-gradient(135deg,#e0b48a,#8a4a2a)}
.review p{position:absolute;left:102px;top:0;width:415px;font-size:12px;line-height:1.6;color:var(--muted)}
.review .who{position:absolute;left:102px;top:74px;font-size:10px;color:#333;line-height:1.8}
.review .stars{position:absolute;left:265px;top:82px;display:flex;gap:4px}

/* footer */
.footer{top:1955px;left:0;width:1200px;height:263px;background:var(--blue)}
.f-col{position:absolute;top:40px;color:#fff;font-size:12px}
.f-col h5{font-size:13px;font-weight:600;margin-bottom:14px;display:flex;align-items:center;gap:8px}
.f-col p{line-height:1.5;color:#dfe6ff}
.f-line{display:flex;align-items:center;gap:12px;margin-top:6px;color:#dfe6ff}
.map{width:232px;height:143px;background:linear-gradient(135deg,#e8e9e2,#cfd3c4)}
.fb{width:245px;background:#eef2fb;border-top:4px solid #fff}
.fb-post{display:flex;gap:10px;padding:8px;border-bottom:3px solid var(--blue)}
.fb-post .pic{width:28px;height:28px;background:#555}
.fb-post div{font-size:10px;color:#333;line-height:1.35}
.fb-post b{color:var(--blue);font-weight:600}
.fb-post small{display:block;color:var(--blue);font-size:8px;margin-top:2px}
.field{width:212px;height:30px;background:#193a9e;color:#dfe6ff;font-size:11px;padding:0 12px;display:flex;align-items:center;justify-content:space-between;margin-top:12px}
.f-btn{margin:20px 0 0 130px;width:82px;height:22px;background:var(--green);color:#fff;font-size:11.5px;font-weight:600;display:flex;align-items:center;justify-content:center}
.bottom{top:2218px;left:0;width:1200px;height:58px;background:var(--blue-deep);color:#8b97c6;font-size:11px;display:flex;align-items:center;justify-content:space-between;padding:0 62px}
.socials{display:flex;gap:12px}
.socials span{width:14px;height:14px;border-radius:50%;background:#fff}
</style>
</head>
<body>

<div class="abs topline"></div>
<div class="abs brand">
  <div class="brand-dot"></div>
  <div class="brand-name">Valley Rescue Academy</div>
</div>
<div class="abs contact-bar">
  <span><svg width="16" height="16" viewBox="0 0 24 24"><path fill="#0b2a8c" d="M6.6 10.8a15 15 0 0 0 6.6 6.6l2.2-2.2c.3-.3.7-.4 1-.2 1.1.4 2.3.6 3.6.6.6 0 1 .4 1 1V20c0 .6-.4 1-1 1A17 17 0 0 1 3 4c0-.6.4-1 1-1h3.5c.6 0 1 .4 1 1 0 1.3.2 2.5.6 3.6.1.3 0 .7-.2 1z"/></svg><i class="sep"></i>916-555-0187</span>
  <span><svg width="20" height="15" viewBox="0 0 20 15"><rect width="20" height="15" rx="1" fill="#0b2a8c"/><path d="M1 1l9 7 9-7" stroke="#fff" stroke-width="1.5" fill="none"/></svg><i class="sep"></i>info@valleyrescue.com</span>
</div>
<div class="abs badge" role="img" aria-label="Accreditation badge"></div>

<nav class="abs nav">
  <a class="active">Home</a><a>Class Calender</a><a>Classes for Groups</a><a>Certification Classes</a><a>About Us</a><a>Policies</a>
</nav>

<div class="abs hero" role="img" aria-label="Photo of a CPR training class with an instructor presenting to seated students"></div>
<div class="abs hero-arrow" style="left:16px"><svg width="12" height="12" viewBox="0 0 12 12"><path d="M8 1L3 6l5 5" stroke="#fff" stroke-width="2" fill="none"/></svg></div>
<div class="abs hero-arrow" style="left:1148px"><svg width="12" height="12" viewBox="0 0 12 12"><path d="M4 1l5 5-5 5" stroke="#fff" stroke-width="2" fill="none"/></svg></div>
<div class="abs hero-tag">Our company specializes in CPR and First Aid Certification Classes</div>

<section class="abs features">
  <div class="feature">
    <h3>Our Classes</h3>
    <ul><li>CPR</li><li>BLS</li><li>CPR+First Aid</li><li>BLS+First Aid</li></ul>
    <span class="btn-white">Read More</span>
  </div>
  <div class="feature">
    <h3>Our Certifications</h3>
    <p>We provide these certifications two ways</p>
    <ul><li>ONSITE-We come to you</li><li>HOSTED-we offer weekly classes</li></ul>
    <span class="btn-outline">Read More</span>
  </div>
  <div class="feature">
    <h3>Appointments</h3>
    <p>Quisque magna sapien, dapibus ac volutpat adipiscing, lacinia varius sapien aliquam facilisis.</p>
    <span class="btn-outline">Register Now</span>
  </div>
  <div class="feature">
    <h3>Schedule</h3>
    <div class="sched-row"><span>Monday - Friday</span><span>8.00 - 18.00</span></div>
    <div class="sched-row"><span>Saturday</span><span>8.00 - 16.00</span></div>
    <div class="sched-row"><span>Sunday</span><span>8.00 - 13.00</span></div>
  </div>
</section>

<h2 class="abs about-title">About Us &amp; What We Do</h2>
<p class="abs about-text">Lorem Ipsum is simply dummy text of the printing and typesetting industry. Lorem Ipsum has been the industry's standard dummy text ever since the 1500s, when an unknown printer took a galley of type and scrambled it to make a type specimen book.</p>

<section class="abs plans">
  <div class="plan">
    <h2>CPR</h2><div class="price">$39</div>
    <div class="icons"><svg width="12" height="14"><circle cx="6" cy="4" r="3.5" fill="#7a808c"/><rect x="1" y="8" width="10" height="6" rx="3" fill="#7a808c"/></svg><svg width="10" height="16"><circle cx="5" cy="3" r="2.5" fill="#7a808c"/><rect x="2" y="6" width="6" height="10" rx="2" fill="#7a808c"/></svg><svg width="14" height="14"><circle cx="5" cy="5" r="4" fill="#7a808c"/><rect x="5" y="7" width="9" height="6" rx="3" fill="#7a808c"/></svg></div>
    <div class="labels">Adult<i>|</i>Child<i>|</i>Infant</div>
    <div class="time">90 Minutes!</div>
    <div class="links"><span class="go">Register Now</span><span>Learn More</span></div>
  </div>
  <div class="plan">
    <h2>BLS</h2><div class="price">$49</div>
    <div class="icons"><svg width="12" height="14"><circle cx="6" cy="4" r="3.5" fill="#7a808c"/><rect x="1" y="8" width="10" height="6" rx="3" fill="#7a808c"/></svg><svg width="12" height="14"><path d="M1 3c0-3 10-3 10 0 0 4-2 5-2 10-1 1-2-4-3-4s-2 5-3 4C3 8 1 7 1 3z" fill="#7a808c"/></svg></div>
    <div class="labels">Health Care<i>|</i>Dental</div>
    <div class="time">90 Minutes!</div>
    <div class="links"><span>Register Now</span><span>Learn More</span></div>
  </div>
  <div class="plan">
    <h2>CPR+First Aid</h2><div class="price">$59</div>
    <div class="icons"><svg width="12" height="14"><circle cx="6" cy="4" r="3.5" fill="#7a808c"/><rect x="1" y="8" width="10" height="6" rx="3" fill="#7a808c"/></svg><svg width="10" height="16"><circle cx="5" cy="3" r="2.5" fill="#7a808c"/><rect x="2" y="6" width="6" height="10" rx="2" fill="#7a808c"/></svg><svg width="14" height="14"><circle cx="5" cy="5" r="4" fill="#7a808c"/><rect x="5" y="7" width="9" height="6" rx="3" fill="#7a808c"/></svg></div>
    <div class="labels">Adult<i>|</i>Child<i>|</i>Infant</div>
    <div class="time">90 Minutes!</div>
    <div class="links"><span>Register Now</span><span>Learn More</span></div>
  </div>
  <div class="plan">
    <h2>BLS+First Aid</h2><div class="price">$69</div>
    <div class="icons"><svg width="12" height="14"><circle cx="6" cy="4" r="3.5" fill="#7a808c"/><rect x="1" y="8" width="10" height="6" rx="3" fill="#7a808c"/></svg><svg width="12" height="14"><path d="M1 3c0-3 10-3 10 0 0 4-2 5-2 10-1 1-2-4-3-4s-2 5-3 4C3 8 1 7 1 3z" fill="#7a808c"/></svg></div>
    <div class="labels">Health Care<i>|</i>Dental</div>
    <div class="time">90 Minutes!</div>
    <div class="links"><span>Register Now</span><span>Learn More</span></div>
  </div>
</section>

<section class="abs lower">
  <h2 class="abs sec-title" style="left:58px;top:35px">Latest News</h2>
  <h2 class="abs sec-title" style="left:625px;top:35px">Reviews</h2>

  <article class="news-item" style="top:108px">
    <div class="news-thumb" role="img" aria-label="News photo of a student studying"></div>
    <div class="news-body">
      <h4>Etiam tristique sagittis pulvinar</h4>
      <div class="meta"><span><svg width="12" height="12"><rect x="1" y="2" width="10" height="9" fill="none" stroke="#0b2a8c" stroke-width="1.5"/><rect x="1" y="2" width="10" height="3" fill="#0b2a8c"/></svg>27 DEC 2013</span><span><svg width="14" height="12"><ellipse cx="6" cy="5" rx="6" ry="4" fill="#0b2a8c"/><path d="M3 8l-1 4 4-3" fill="#0b2a8c"/></svg>3</span></div>
      <p>Integer iaculis egestas odio, vel dictum turpis placerat id ellentesque semper nisl eget odio eleifend, nec blandit libero porta aliquam vel vehicula dui nam sit amet ultricies sapien.</p>
      <div class="posted">Posted in: General, Health</div>
    </div>
  </article>

  <article class="news-item" style="top:343px">
    <div class="news-thumb" role="img" aria-label="News photo of a classroom" style="background:linear-gradient(135deg,#8fae7a,#3d5a3a)"></div>
    <div class="news-body">
      <h4>Nullam commodo felis id</h4>
      <div class="meta"><span><svg width="12" height="12"><rect x="1" y="2" width="10" height="9" fill="none" stroke="#0b2a8c" stroke-width="1.5"/><rect x="1" y="2" width="10" height="3" fill="#0b2a8c"/></svg>25 DEC 2013</span><span><svg width="14" height="12"><ellipse cx="6" cy="5" rx="6" ry="4" fill="#0b2a8c"/><path d="M3 8l-1 4 4-3" fill="#0b2a8c"/></svg>5</span></div>
      <p>Integer iaculis egestas odio, vel dictum turpis placerat id ellentesque semper nisl eget odio eleifend, nec blandit libero porta aliquam vel vehicula dui nam sit amet ultricies sapien.</p>
      <div class="posted">Posted in: General, Health</div>
      <div class="show-all" style="margin-top:12px">Show All »</div>
    </div>
  </article>

  <div class="review" style="top:101px">
    <div class="avatar" role="img" aria-label="Reviewer portrait"></div>
    <p>Integer iaculis egestas odio, vel dictum turpis placerat id ellentesque semper nisl eget odio eleifend, nec blandit libero porta aliquam vel vehicula dui nam sit amet ultricies sapien.</p>
    <div class="who">Jordan- CA, United States<br>August 18, 2014</div>
    <svg class="stars" width="120" height="18" viewBox="0 0 120 18"><g fill="#f2c200"><path id="st" d="M9 1l2.4 5 5.4.6-4 3.7 1.1 5.4L9 13l-4.9 2.7 1.1-5.4-4-3.7 5.4-.6z"/><use href="#st" x="24"/><use href="#st" x="48"/><use href="#st" x="72"/></g><use href="#st" x="96" fill="none" stroke="#f2c200"/></svg>
  </div>
  <div class="review" style="top:250px">
    <div class="avatar" role="img" aria-label="Reviewer portrait" style="background:linear-gradient(135deg,#f0c98e,#7a4a28)"></div>
    <p>Integer iaculis egestas odio, vel dictum turpis placerat id ellentesque semper nisl eget odio eleifend, nec blandit libero porta aliquam vel vehicula dui nam sit amet ultricies sapien.</p>
    <div class="who">Jordan- CA, United States<br>August 18, 2014</div>
    <svg class="stars" width="120" height="18" viewBox="0 0 120 18"><g fill="#f2c200"><use href="#st"/><use href="#st" x="24"/><use href="#st" x="48"/><use href="#st" x="72"/></g><use href="#st" x="96" fill="none" stroke="#f2c200"/></svg>
  </div>
  <div class="review" style="top:407px">
    <div class="avatar" role="img" aria-label="Reviewer portrait" style="background:linear-gradient(135deg,#f6b93b,#b8731f)"></div>
    <p>Integer iaculis egestas odio, vel dictum turpis placerat id ellentesque semper nisl eget odio eleifend, nec blandit libero porta aliquam vel vehicula dui nam sit amet ultricies sapien.</p>
    <div class="who">Jordan- CA, United States<br>August 18, 2014</div>
    <svg class="stars" width="120" height="18" viewBox="0 0 120 18"><g fill="#f2c200"><use href="#st"/><use href="#st" x="24"/><use href="#st" x="48"/><use href="#st" x="72"/></g><use href="#st" x="96" fill="none" stroke="#f2c200"/></svg>
  </div>
  <div class="abs show-all" style="left:727px;top:546px;color:#555">Show All »</div>
</section>

<footer class="abs footer">
  <div class="f-col" style="left:58px;width:240px">
    <h5>GET IN TOUCH</h5>
    <p>Doloreiur quia commolu ptatemp dolupta oreprerum tibusam eumenis et consent accullignis dentibea</p>
    <div class="f-line" style="margin-top:14px"><svg width="10" height="13"><path d="M5 0a5 5 0 0 1 5 5c0 3-5 8-5 8S0 8 0 5a5 5 0 0 1 5-5z" fill="#dfe6ff"/><circle cx="5" cy="5" r="2" fill="#0b2a8c"/></svg>4820 Alder Creek Rd #110</div>
    <div class="f-line"><svg width="11" height="11" viewBox="0 0 24 24"><path fill="#dfe6ff" d="M6.6 10.8a15 15 0 0 0 6.6 6.6l2.2-2.2c.3-.3.7-.4 1-.2 1.1.4 2.3.6 3.6.6.6 0 1 .4 1 1V20c0 .6-.4 1-1 1A17 17 0 0 1 3 4c0-.6.4-1 1-1h3.5c.6 0 1 .4 1 1 0 1.3.2 2.5.6 3.6.1.3 0 .7-.2 1z"/></svg>916-555-0187</div>
    <div class="f-line"><svg width="11" height="9"><rect width="11" height="9" fill="#dfe6ff"/><path d="M0 0l5.5 5L11 0" stroke="#0b2a8c" fill="none"/></svg>info@valleyrescue.com</div>
  </div>
  <div class="f-col" style="left:354px">
    <h5>FIND US</h5>
    <div class="map" role="img" aria-label="Street map showing the training location"></div>
  </div>
  <div class="f-col" style="left:630px">
    <h5><span style="display:inline-block;width:13px;height:13px;background:#4a6fd0"></span>FOLLOW US</h5>
    <div class="fb">
      <div class="fb-post"><span class="pic" role="img" aria-label="Profile picture"></span><div><b>Dan Mercer</b><br>Fusce eu lorem dui. Integer eu venen atis lectus sed blandit urna<small>Like :: Comment</small></div></div>
      <div class="fb-post"><span class="pic" role="img" aria-label="Profile picture"></span><div><b>Dan Mercer</b><br>Fusce eu lorem dui. Integer eu venen atis lectus sed blandit urna<small>Like :: Comment</small></div></div>
    </div>
  </div>
  <div class="f-col" style="left:924px;width:214px">
    <h5>CONTACT</h5>
    <p>Doloreiur quia commolu ptatemp dolupta oreprerum</p>
    <div class="field" style="margin-top:16px">Email</div>
    <div class="field">Contact For <svg width="10" height="6"><path d="M1 1l4 4 4-4" stroke="#dfe6ff" fill="none"/></svg></div>
    <div class="f-btn">CONTACT</div>
  </div>
</footer>

<div class="abs bottom">
  <span>© 2015 yoursite. All rights reserved.</span>
  <div class="socials"><span></span><span></span><span></span><span></span></div>
</div>

</body>
</html>
```